Web and Logo Design for eCommerce site

We're launching a sister brand and require a full design for the site.

The site must have an established feel and appeal to corporate and institutional buyers.
Updates

Just a note about the wireframe design:

The Search & Rescue / Coast Guard / NVDK, etc. in the header area aren't buttons or menu items, but rather just info (along the lines of a tagline).  Sort of a "who we serve" sort of thing.

Worth noting is that it's specifically geared towards LARGE BUYERS.  For example, a police force buying 200 headlamps and 85 pairs of gloves.  So they'll register + sign in and then add a bunch of items to a RFQ.

Aim for a professional, masculine design.

Target Market(s)

We will be selling outdoor gear to the military, law enforcement, fire and rescue and first responders.

Requirements
Must have
• We require:
- Logo (vector based)

Site:
- template page
* main site template, re-skinned version of our current site
* horizontal drop-down menu
- product listings page
* thumbnail view of products
- product details page
* including elements such as product image, color/size selector, descriptions and specs (again, based loosely on our current website)
- account management page
* illustrating basic data entry styles for text box, buttons, grid, etc.

The site needs to be given a responsive design, so 2 versions of each design should be presented for desktop + mobile views.

Additional funds are available if the designer is able to fully implement the designs into a responsive framework such as bootstrap.

Nice to have
• Clean, professional design similar to:

http://military.trailvexagear.com/gov/accessories/gloves.html

http://leaf.ombrivo.com/ProductFind.aspx?language=EN&category=Hardshell&subcat=Waterproof_Jackets

```html
<!DOCTYPE html>
<html lang="en">
<head>
<meta charset="utf-8">
<title>NorGuard – Outdoor Gear for First Responders</title>
<link href="https://fonts.googleapis.com/css2?family=Source+Sans+3:wght@400;600;700&display=swap" rel="stylesheet">
<style>
:root{
  --page:#f3f3f3;
  --ink:#4a4a4a;
  --muted:#8a8a8a;
  --purple:#8a6fa8;
  --purple-dark:#6f5690;
  --nav-ink:#ece6f3;
  --sub-nav:#ececec;
  --line:#d6d6d6;
  --price:#3a86c8;
  --footer:#5c4a7a;
  --footer-dark:#4a3b63;
  --footer-ink:#d8d0e4;
  --modal:#222222;
  --modal-edge:#4aa8e0;
  --btn-top:#4aa8e6;
  --btn-bottom:#2a7fc4;
  --dim:rgba(0,0,0,.62);
}
*{box-sizing:border-box;margin:0;padding:0}
html,body{width:978px;height:1200px;overflow:hidden}
body{font-family:"Source Sans 3",sans-serif;background:var(--page);color:var(--ink)}
.page{position:relative;width:978px;height:1200px;overflow:hidden;background:var(--page)}
.abs{position:absolute}

.brand{left:65px;top:28px;font-size:38px;font-weight:700;color:#5a4778;letter-spacing:.5px}
.login{left:655px;top:36px;width:75px;height:30px;background:#2e6fa8;color:#fff;font-size:13px;display:flex;align-items:center;justify-content:center;border-radius:2px}
.tagline{left:742px;top:33px;font-size:14px;line-height:18px;color:#888}

.serve{left:65px;top:85px;width:848px;height:33px;background:linear-gradient(var(--purple),var(--purple-dark));display:flex}
.serve span{flex:1;color:var(--nav-ink);font-size:12.5px;display:flex;align-items:center;justify-content:center;border-right:1px solid rgba(255,255,255,.18)}
.serve span:last-child{border-right:0}

.menu{left:65px;top:118px;width:848px;height:39px;background:var(--sub-nav);display:flex;border-bottom:1px solid var(--line)}
.menu a{flex:auto;color:#555;font-size:12.5px;text-decoration:none;display:flex;align-items:center;justify-content:center;border-right:1px solid var(--line)}
.menu a:last-child{border-right:0}

.hero{left:65px;top:157px;width:847px;height:314px;background:linear-gradient(90deg,#3d4636 0%,#6d6a60 35%,#9a9a98 60%,#7d7d7c 100%)}

.sidebar{left:65px;top:484px;width:182px;height:352px;border:1px solid var(--line);background:#fafafa}
.sidebar h2{height:31px;background:linear-gradient(var(--purple),var(--purple-dark));color:#fff;font-size:14px;font-weight:400;padding:6px 16px}
.sidebar h3{font-size:12px;font-weight:400;color:#555;margin:14px 0 6px 17px}
.sidebar li{list-style:none;font-size:10px;color:#777;margin:0 0 8px 19px}

.grid{left:259px;top:484px;width:657px;height:428px;display:grid;grid-template-columns:repeat(4,1fr);grid-template-rows:repeat(2,1fr);border:1px solid var(--line);background:#fafafa}
.card{border-right:1px solid var(--line);border-bottom:1px solid var(--line);position:relative}
.card:nth-child(4n){border-right:0}
.card:nth-child(n+5){border-bottom:0}
.thumb{position:absolute;left:38px;top:14px;width:88px;height:126px;border-radius:14px 14px 6px 6px}
.camo{background:linear-gradient(135deg,#6b6a4c,#8a7f5c 50%,#5c5a40)}
.olive{background:linear-gradient(#8a8560,#6e6a4a)}
.glove{top:20px;height:112px;border-radius:20px}
.card .name{position:absolute;left:0;right:0;top:163px;text-align:center;font-size:13px;color:#999}
.card .price{position:absolute;left:0;right:0;top:180px;text-align:center;font-size:15px;font-weight:600;color:var(--price)}

.footer{left:0;top:943px;width:978px;height:213px;background:linear-gradient(var(--footer),var(--footer-dark))}
.col{top:977px}
.col h4{font-size:13px;font-weight:600;color:var(--footer-ink);margin-bottom:6px}
.col li{list-style:none;font-size:10px;color:#a99cbd;margin-bottom:8px}
.find{left:555px;top:999px;width:194px;height:23px;background:#fff;border:1px solid #ccc;font-size:9px;color:#999;padding:4px 8px}
.find b{position:absolute;right:4px;top:3px;width:46px;height:15px;background:#2e6fa8;color:#fff;font-weight:400;font-size:8px;display:flex;align-items:center;justify-content:center}
.social{left:556px;top:1036px;display:flex;gap:4px}
.social i{width:23px;height:23px;border-radius:50%;background:#e4e0ea}
.legal{left:0;top:1156px;width:978px;height:44px;background:#3e3252;color:#9a8fb0;font-size:9px;padding:15px 73px}

.dim{inset:0;background:var(--dim)}
.modal{left:219px;top:331px;width:532px;height:200px;border:2px solid var(--modal-edge);background:var(--modal);padding:10px}
.modal-inner{width:100%;height:100%;border:1px solid #4a7fa0;text-align:center;color:#fff;padding-top:38px}
.modal .lead{font-size:15.5px}
.modal .body{font-size:12px;line-height:22px}
.register{display:inline-flex;margin-top:15px;width:134px;height:32px;align-items:center;justify-content:center;background:linear-gradient(var(--btn-top),var(--btn-bottom));font-size:14px;color:#fff}
</style>
</head>
<body>
<div class="page">
  <div class="abs brand">NorGuard</div>
  <div class="abs login">LOGIN</div>
  <div class="abs tagline">Great Outdoor Gear for<br>Canada's First Responders</div>

  <div class="abs serve">
    <span>SEARCH &amp; RESCUE</span><span>COAST GUARD</span><span>NVDK</span><span>FIRE</span><span>MILITARY</span><span>LAW ENFORCEMENT</span>
  </div>
  <nav class="abs menu">
    <a>RESCUE GEAR</a><a>FOOTWEAR</a><a>CLOTHING</a><a>TENTS, MATS, SLEEPING BAGS</a><a>CAMPING GEAR</a><a>SNOW SPORTS</a><a>BRANDS</a>
  </nav>

  <div class="abs hero" role="img" aria-label="Responder in a grey fleece jacket wearing a radio and rescue tools, forest background"></div>

  <aside class="abs sidebar">
    <h2>SHOP NOW</h2>
    <h3>CATEGORY</h3>
    <ul><li>Mitts (5)</li><li>Liners (8)</li><li>Touch Screen (5)</li></ul>
    <h3>PRODUCT HIGHLIGHTS</h3>
    <ul><li>Insulation (8)</li><li>Shell (1)</li><li>Waterproof (12)</li><li>Soft Shell (2)</li><li>Windproof (12)</li><li>Fleece (11)</li><li>Sun Protection (1)</li><li>Touch-Screen Compatible (5)</li></ul>
  </aside>

  <section class="abs grid">
    <div class="card"><div class="thumb camo" role="img" aria-label="Camouflage jacket"></div><div class="name">PRDOUCT TITTLE</div><div class="price">$217.00</div></div>
    <div class="card"><div class="thumb olive" role="img" aria-label="Olive jacket"></div><div class="name">PRDOUCT TITTLE</div><div class="price">$217.00</div></div>
    <div class="card"><div class="thumb camo" role="img" aria-label="Camouflage jacket"></div><div class="name">PRDOUCT TITTLE</div><div class="price">$217.00</div></div>
    <div class="card"><div class="thumb olive" role="img" aria-label="Olive hooded jacket"></div><div class="name">PRDOUCT TITTLE</div><div class="price">$217.00</div></div>
    <div class="card"><div class="thumb camo glove" role="img" aria-label="Pair of camouflage gloves"></div><div class="name">PRDOUCT TITTLE</div><div class="price">$217.00</div></div>
    <div class="card"><div class="thumb camo glove" role="img" aria-label="Pair of camouflage mitts"></div><div class="name">PRDOUCT TITTLE</div><div class="price">$217.00</div></div>
    <div class="card"><div class="thumb olive glove" role="img" aria-label="Pair of olive gauntlet gloves"></div><div class="name">PRDOUCT TITTLE</div><div class="price">$217.00</div></div>
    <div class="card"><div class="thumb camo glove" role="img" aria-label="Pair of brown mitts"></div><div class="name">PRDOUCT TITTLE</div><div class="price">$217.00</div></div>
  </section>

  <footer class="abs footer"></footer>
  <div class="abs col" style="left:80px"><h4>CUSTOMER</h4><ul><li>Infinite Guarantee</li><li>Shipping</li><li>Returns</li><li>FAQ</li><li>Find A Dealer</li></ul></div>
  <div class="abs col" style="left:230px"><h4>PRODUCTS</h4><ul><li>Rescue Gear</li><li>Footwear</li><li>Clothing</li><li>Tents, Mats &amp; Sleeping bags</li><li>Camping Gear</li></ul></div>
  <div class="abs col" style="left:417px"><h4>HELP &amp; FAQ</h4><ul><li>FAQ</li><li>Sizing Charts</li><li>Product Care</li><li>Warranty Policy</li></ul></div>
  <div class="abs col" style="left:554px"><h4>FIND A STORE</h4></div>
  <div class="abs find">Email address<b>FIND</b></div>
  <div class="abs social"><i></i><i></i><i></i><i></i></div>
  <div class="abs legal">© 2014 Company Name. All right reserved. Term of Use</div>

  <div class="abs dim"></div>
  <div class="abs modal">
    <div class="modal-inner">
      <p class="lead">Please register to enter and enjoy Canada’best selection of outdoor</p>
      <p class="body">gear at special pricing and terms that reflect your commitment to service and duty,<br>your unique position and credentials</p>
      <span class="register">REGISTER</span>
    </div>
  </div>
</div>
</body>
</html>
```